Meadowlight Soaps Business Card

The new business card design will incorporate my new logo components designed by one of your designers. Meadowlight Soaps creates high quality soaps and bath products. They would be suited for a Spa, Bed and Breakfast, Boutique environment. The look should be a white background.
Classy, soft and using the colour palet of the logo. The card will be two sided.

Reason: Need more time to make some changes and decide.

Target Market(s)

Looking to appeal to an upper end market. Spas, boutiques, independent gift stores, bridal salons, bed and breakfast, etc. I want the card to impart a sense of elegance, tranquility and Meadowlight. But also quality and value.

Industry/Entity Type

Business

Font styles to use
Sans Serif
Script

Requirements
Must have
• My logo on the front. But also on the back but faded out to allow written notes on the back.
On the front : Carol Pritchett
Owner/Creator
48 Fenwick Rd
Guelph, Ont N4K 2P9
519.402.6183
Creating Quality Handcrafted Soaps And Bath Products
Custom and Wholesale Orders Welcome
Www.meadowlightsoaps.ca
www.friendpage.com / MeadowlightSoapandBath
info@meadowlightsoaps.ca

```html
<!DOCTYPE html>
<html lang="en">
<head>
<meta charset="utf-8">
<title>Meadowlight Soaps Business Card</title>
<link rel="stylesheet" href="https://fonts.googleapis.com/css2?family=Great+Vibes&family=Lato:wght@300;400&display=swap">
<style>
  :root {
    --page: #efece7;
    --card: #fcfcfb;
    --sage: #8dbdb2;
    --sage-soft: #bcd8d1;
    --blush: #e6d2c6;
    --ink: #2f3133;
    --muted: #6b6f70;
    --rule: #c9d9d5;
  }
  html, body {
    margin: 0; padding: 0;
    width: 1200px; height: 858px;
    overflow: hidden;
    background: var(--page);
    font-family: "Lato", sans-serif;
  }
  .canvas {
    position: relative;
    width: 1200px; height: 858px;
    display: flex; flex-direction: column;
    align-items: center; justify-content: center;
    gap: 56px;
  }
  .card {
    position: relative;
    width: 560px; height: 320px;
    background: var(--card);
    box-shadow: 0 4px 14px rgba(0,0,0,.12);
    overflow: hidden;
  }
  /* front */
  .brand {
    position: absolute; left: 0; top: 0;
    width: 250px; height: 270px;
    display: flex; flex-direction: column; align-items: center; justify-content: center;
    gap: 14px;
  }
  .brand-mark {
    width: 120px; height: 120px; border-radius: 50%;
    background: radial-gradient(circle at 45% 40%, var(--sage-soft), var(--blush) 60%, transparent 72%);
  }
  .brand-name {
    font-family: "Lato", sans-serif; font-weight: 300;
    font-size: 22px; color: var(--sage); letter-spacing: .5px;
  }
  .divider {
    position: absolute; left: 250px; top: 40px;
    width: 1px; height: 190px; background: var(--rule);
  }
  .details {
    position: absolute; left: 285px; top: 38px; right: 20px;
  }
  .person-name {
    font-family: "Great Vibes", cursive; font-size: 34px;
    color: var(--sage); line-height: 1;
  }
  .person-role {
    font-size: 12px; color: var(--muted); margin: 2px 0 20px 4px;
  }
  .contact { list-style: none; margin: 0; padding: 0; font-size: 11.5px; color: var(--ink); }
  .contact li { display: flex; align-items: flex-start; gap: 8px; line-height: 1.45; margin-bottom: 8px; }
  .contact svg { flex: none; width: 11px; height: 11px; margin-top: 3px; fill: var(--ink); }
  .contact .group li { margin-bottom: 2px; }
  .tagline-band {
    position: absolute; left: 0; right: 0; bottom: 0; height: 50px;
    background: var(--sage);
    display: flex; align-items: center; justify-content: center;
    color: #fff; font-weight: 300; font-size: 18px; letter-spacing: .3px;
  }
  /* back */
  .faded-logo {
    position: absolute; inset: 0;
    background:
      radial-gradient(ellipse at 30% 55%, rgba(141,189,178,.22), transparent 55%),
      radial-gradient(ellipse at 70% 40%, rgba(230,210,198,.3), transparent 50%);
  }
  .note-title {
    position: absolute; left: 0; right: 0; top: 40px;
    text-align: center; font-size: 24px; color: var(--ink); font-weight: 400;
  }
  .note-lines {
    position: absolute; left: 60px; right: 60px; top: 110px;
    display: flex; flex-direction: column; gap: 46px;
  }
  .note-line { border-top: 2px dotted var(--ink); }
</style>
</head>
<body>
<main class="canvas">
  <section class="card card-front">
    <div class="brand">
      <div class="brand-mark" role="img" aria-label="Soft watercolour tree logo in sage and blush"></div>
      <div class="brand-name">Meadowlight Soaps</div>
    </div>
    <div class="divider"></div>
    <div class="details">
      <div class="person-name">Carol Pritchett</div>
      <div class="person-role">Owner</div>
      <ul class="contact">
        <li>
          <svg viewBox="0 0 12 12"><path d="M6 0a4 4 0 0 0-4 4c0 3 4 8 4 8s4-5 4-8a4 4 0 0 0-4-4zm0 5.5A1.5 1.5 0 1 1 6 2.5a1.5 1.5 0 0 1 0 3z"/></svg>
          <span>48 Fenwick Rd<br>Guelph, Ont N4K 2P9</span>
        </li>
        <li>
          <svg viewBox="0 0 12 12"><path d="M2.5 0l2 2.5-1.2 1.5c.8 1.8 2 3 3.8 3.8L8.6 6.6 11 8.5 9.7 11C4.8 10.5 1 6.8.6 2z"/></svg>
          <span>519.402.6183</span>
        </li>
        <li>
          <svg viewBox="0 0 12 12"><circle cx="6" cy="6" r="6"/></svg>
          <span>www.meadowlightsoaps.ca</span>
        </li>
        <li>
          <svg viewBox="0 0 12 12"><rect width="12" height="12"/></svg>
          <span>www.friendpage.com /MeadowlightSoapandBath</span>
        </li>
      </ul>
    </div>
    <div class="tagline-band">Creating Quality Handcrafted Soaps And Bath Products</div>
  </section>

  <section class="card card-back">
    <div class="faded-logo" role="img" aria-label="Faded watercolour tree logo as background for notes"></div>
    <h2 class="note-title">Note</h2>
    <div class="note-lines">
      <div class="note-line"></div>
      <div class="note-line"></div>
      <div class="note-line"></div>
      <div class="note-line"></div>
    </div>
  </section>
</main>
</body>
</html>
```